Verdana Crest New Website - Online Learning and Education

New Wordpress website for an online learning site that has courses, worksheets, quizzes, etc.
Updates

We would like something similar to this website: https://hallowaybridgeinstitute.example/mediation-skills-course/. But continue with the content of our current website: http://verdanacrestlearninghub.example

We would like something similar to this site: https://hallowaybridgeinstitute.example/mediation-skills-course/

Coding

Coded - Design and coding required

```html
<!DOCTYPE html>
<html lang="en">
<head>
<meta charset="utf-8">
<title>Verdana Crest – Online Learning</title>
<link href="https://fonts.googleapis.com/css2?family=Open+Sans:wght@400;600;700&family=Raleway:wght@700;800&display=swap" rel="stylesheet">
<style>
:root{
  --red:#c8202f;
  --navy:#1d3f72;
  --ink:#333a44;
  --muted:#6b7280;
  --dark:#1b1b1d;
  --light:#f4f5f7;
  --line:#e3e5e8;
  --white:#ffffff;
}
*{box-sizing:border-box;margin:0;padding:0}
html,body{width:702px;height:1200px;overflow:hidden;background:var(--white)}
body{font-family:"Open Sans",Arial,sans-serif;color:var(--ink);font-size:9px;line-height:1.55}
.page{width:702px;height:1200px;position:relative}
.site-header{height:72px;display:flex;align-items:center;justify-content:space-between;padding:0 42px}
.brand{display:flex;align-items:center;gap:8px;font-family:"Raleway",sans-serif;font-weight:800;font-size:19px;color:var(--navy);letter-spacing:.5px}
.brand-mark{width:14px;height:14px;border-radius:50%;background:var(--red)}
.main-nav{display:flex;gap:26px;font-size:8px;font-weight:600;text-transform:uppercase;color:var(--ink)}
.main-nav .active{color:var(--red)}
.hero{position:relative;height:268px;background:linear-gradient(100deg,#6f7a80 0%,#a2a9ad 40%,#c9c4bd 65%,#8a7d74 100%);padding:82px 42px 0}
.hero-title{font-family:"Raleway",sans-serif;font-weight:800;font-size:30px;color:var(--white);line-height:1.1}
.hero-sub{font-size:13px;font-weight:600;color:var(--white);margin-top:4px}
.btn-launch{display:inline-block;margin-top:12px;background:var(--red);color:var(--white);font-size:7px;font-weight:700;text-transform:uppercase;padding:6px 12px}
.hero-dots{position:absolute;left:42px;bottom:18px;display:flex;gap:5px}
.hero-dots span{width:6px;height:6px;border-radius:50%;background:rgba(255,255,255,.55)}
.hero-dots span:first-child{background:var(--white)}
.content{display:flex;gap:22px;padding:30px 42px 0;height:575px}
.col-main{width:400px}
.col-side{width:196px}
h2{font-family:"Raleway",sans-serif;font-weight:800;font-size:14px;color:var(--navy);text-transform:uppercase;margin-bottom:8px}
.col-main p{margin-bottom:8px}
.topic-list{list-style:none;margin:4px 0 18px}
.topic-list li{display:flex;align-items:center;gap:8px;height:17px}
.topic-list li::before{content:"";width:8px;height:8px;border-radius:50%;background:var(--navy)}
.help-box{margin-top:14px;background:var(--dark);height:86px;color:var(--white);text-align:center;padding-top:24px}
.help-box h3{font-family:"Raleway",sans-serif;font-weight:800;font-size:16px}
.help-box p{font-size:7.5px;color:#c9cbd0;margin:2px 0 0}
.video{height:132px;margin:6px 0 24px;background:linear-gradient(135deg,#5d6468,#9aa1a4);display:flex;align-items:center;justify-content:center}
.screen{height:112px;margin-bottom:12px;background:linear-gradient(180deg,#e9ebee,#f7f7f8);border:1px solid var(--line)}
.subscribe{position:absolute;top:912px;left:0;width:702px;height:50px;background:var(--red);display:flex;align-items:center;padding:0 42px;color:var(--white);font-weight:700;font-size:9px;text-transform:uppercase}
.subscribe-field{margin-left:10px;width:150px;height:18px;background:var(--white);color:var(--muted);font-weight:400;text-transform:none;font-size:7px;padding:3px 6px}
.subscribe-btn{background:var(--dark);height:18px;padding:3px 9px;font-size:7px}
.follow{margin-left:auto;display:flex;align-items:center;gap:9px}
.follow i{width:14px;height:14px;border-radius:50%;background:var(--white);display:block}
.site-footer{position:absolute;top:980px;left:0;width:702px;display:flex;padding:0 42px;gap:28px;color:var(--muted);font-size:7.5px}
.foot-brand{width:170px}
.foot-brand .brand{font-size:15px;margin-bottom:10px}
.site-footer h4{font-size:8px;color:var(--navy);text-transform:uppercase;margin-bottom:6px}
.links{display:grid;grid-template-columns:50px 50px;row-gap:4px}
.stack div{margin-bottom:4px}
.bottom-line{position:absolute;top:1172px;left:42px;width:618px;border-top:1px solid var(--line)}
</style>
</head>
<body>
<div class="page">
  <header class="site-header">
    <div class="brand"><span class="brand-mark"></span>Verdana Crest</div>
    <nav class="main-nav"><span class="active">Home</span><span>About Us</span><span>My Profile</span><span>Report an Issue</span></nav>
  </header>

  <section class="hero" role="img" aria-label="Photo of a student studying with a laptop at a desk">
    <h1 class="hero-title">Welcome to Verdana Crest</h1>
    <div class="hero-sub">Get Your Bearings. Plan Your Course.</div>
    <span class="btn-launch">Ready to Launch</span>
    <div class="hero-dots"><span></span><span></span><span></span></div>
  </section>

  <main class="content">
    <div class="col-main">
      <h2>Welcome to Verdana Crest!</h2>
      <p>Verdana Crest, our professional online learning academy and resource library for growing teams, is an online learning application geared toward corporate customers, allowing their employees to identify and cultivate new skills that will be valuable in both their professional and personal lives. Named after the guiding peak, Verdana Crest can help your people get their bearings for where they're headed, and then help them plan a course to get there.</p>
      <p>Concentrating on subjects that are useful to each student not only in the business world but also in life as well, Verdana Crest offers courses on various topics including:</p>
      <ul class="topic-list">
        <li>Become a Better Listener</li>
        <li>Proactive Decision Making</li>
        <li>Improving Self-Awareness</li>
        <li>The Power of Priorities</li>
        <li>Mastering Habits</li>
        <li>Managing a To-Do List</li>
        <li>Perfection: The Enemy of Progress</li>
      </ul>
      <h2>Different Learning Styles</h2>
      <p>Verdana Crest realizes that different people learn in different ways, so we strive to accommodate that. The courses within Verdana Crest include various methods of information dissemination in order to allow for different learning styles: some reading, some video, some reflection, some group activities, and some journaling. Each course includes a brief quiz to ensure you've absorbed the important information. And, if your organization chooses to work through these courses together as a group, that will further enhance your team's learning experience.</p>
      <div class="help-box">
        <h3>HOW CAN WE HELP?</h3>
        <p>Contact us or click "Report an Issue" link in the menu bar above.</p>
      </div>
    </div>
    <aside class="col-side">
      <h2>Overview Video</h2>
      <p>You can view our 4-minute introductory video</p>
      <div class="video" role="img" aria-label="Introductory video preview">
        <svg width="34" height="34" viewBox="0 0 34 34"><path d="M11 7 L28 17 L11 27 Z" fill="#ffffff"/></svg>
      </div>
      <h2>Sample Screens</h2>
      <div class="screen" role="img" aria-label="Sample course screen"></div>
      <div class="screen" role="img" aria-label="Sample quiz screen"></div>
    </aside>
  </main>

  <section class="subscribe">
    Subscribe Email
    <span class="subscribe-field">Enter Email Address</span>
    <span class="subscribe-btn">Subscribe</span>
    <div class="follow">Follow Us <i></i><i></i><i></i><i></i><i></i></div>
  </section>

  <footer class="site-footer">
    <div class="foot-brand">
      <div class="brand"><span class="brand-mark"></span>Verdana Crest</div>
      <div>Copyright © 2020, Verdana Crest.</div>
      <div>All Right reserved</div>
    </div>
    <div>
      <h4>Quick Links</h4>
      <div class="links"><span>Home</span><span>Blog</span><span>About Us</span><span>Reviews</span><span>Services</span><span>Contact Us</span></div>
    </div>
    <div class="stack">
      <h4>Resources</h4>
      <div>Course guides</div><div>Learning library</div><div>Quiz archive</div><div>Worksheet packs</div>
    </div>
    <div class="stack">
      <h4>Contact Info</h4>
      <div>14 Maple Row, Harbor Street,<br>Lakeside City</div>
      <div>1 800 555 0142</div>
      <div>hello@verdanacrest.example</div>
    </div>
  </footer>
  <div class="bottom-line"></div>
</div>
</body>
</html>
```